Redesign ideas for already developed financial iOS app

We are looking for design ideas for an app that we have coded, but which needs a fresh look and feel and some improvement of the navigation and UIX (screenshots uploaded).

The app enables investors to rank investment ideas/stocks based on their ethical & spiritual importance to them, and provides users with a resulting overall “Lumen Tally" for the ranked securities/investments.

Our company, Quillbarrow.com has been associated with transparency since 2001 when we made the performance of Wall Street analysts public and helped regulators uncover substantial conflicts of interest.

We subsequently helped investors discover "independent research". Our data on analyst performance is currently provided to millions of investors through our broker partners. Throughout our history we have empowered investors by making the performance of those they get advice from transparent.

The final design should communicate ease, security and simplicity.

IMPORTANT: The main focus of any design proposals should be the "Shares Sifter". You can find a screenshot of this screen here again: http://clipvault-example.com/t/QW8rTmBkZ

Good luck and thank you for joining us in our mission.

Target Market(s)

Retail investors

Industry/Entity Type

Financial

Requirements
Must have
• easy of use, simplcity
Nice to have
• interactive design
Should not have
• over-complicated

```html
<!DOCTYPE html>
<html lang="en">
<head>
<meta charset="utf-8">
<title>25 Resonant Brands</title>
<link rel="stylesheet" href="https://fonts.googleapis.com/css2?family=Arimo:wght@400;700&family=Playfair+Display:ital,wght@0,700;1,400&display=swap">
<style>
  :root {
    --bg: #ffffff;
    --title-pink: #e0267a;
    --legend-red: #c8344a;
    --ink: #111111;
    --index-line: #1d2230;
    --peer-line: #8b8f97;
    --market-line: #f3e33c;
    --grid: #d9dadd;
    --axis-text: #6d7078;
    --tab-blue: #2a86c8;
    --tab-text: #444444;
    --rule: #cfd0d3;
    --dot-active: #2a9be0;
    --dot-idle: #b8bbc0;
  }
  * { margin: 0; padding: 0; box-sizing: border-box; }
  html, body { width: 857px; height: 1200px; overflow: hidden; background: var(--bg); }
  .screen { position: relative; width: 857px; height: 1200px; background: var(--bg); }

  .screen-title {
    position: absolute; top: 24px; left: 0; width: 100%;
    text-align: center;
    font-family: "Playfair Display", serif; font-weight: 700;
    font-size: 31px; color: var(--title-pink);
  }

  .chart { position: absolute; top: 66px; left: 0; width: 857px; height: 500px; }
  .axis-label { font-family: "Arimo", sans-serif; font-size: 11px; fill: var(--axis-text); }
  .axis-label.current { font-weight: 700; fill: var(--ink); }
  .legend-label { font-family: "Playfair Display", serif; font-style: italic; font-size: 20px; fill: var(--legend-red); }

  .pager { position: absolute; top: 560px; right: 50px; display: flex; gap: 7px; }
  .pager-dot { width: 10px; height: 10px; border-radius: 50%; background: var(--dot-idle); }
  .pager-dot.active { background: var(--dot-active); }

  .tabs {
    position: absolute; top: 578px; left: 0; width: 857px; height: 92px;
    display: flex; align-items: center;
    border-top: 1px solid var(--rule);
    font-family: "Arimo", sans-serif;
  }
  .tab { height: 100%; display: flex; align-items: center; justify-content: center; text-align: center; color: var(--tab-text); }
  .tab + .tab { border-left: 2px solid var(--rule); }
  .tab-description { width: 300px; justify-content: flex-start; padding-left: 24px; color: var(--tab-blue); font-size: 29px; text-decoration: underline; text-underline-offset: 5px; }
  .tab-snapshot { width: 262px; font-size: 25px; line-height: 1.05; }
  .tab-components { width: 295px; font-size: 29px; }

  .description {
    position: absolute; top: 682px; left: 18px; width: 825px;
    font-family: "Arimo", sans-serif; font-weight: 700;
    font-size: 27px; line-height: 31px; color: var(--ink);
  }
</style>
</head>
<body>
<main class="screen">
  <h1 class="screen-title">25 Resonant Brands</h1>

  <svg class="chart" viewBox="0 0 857 500" aria-label="Index performance compared with Broadline 500 performance">
    <g class="grid" stroke="var(--grid)" stroke-width="1">
      <line x1="30" y1="40" x2="785" y2="40"/>
      <line x1="30" y1="150" x2="785" y2="150"/>
      <line x1="30" y1="205" x2="785" y2="205"/>
      <line x1="30" y1="260" x2="785" y2="260"/>
      <line x1="30" y1="315" x2="785" y2="315"/>
      <line x1="30" y1="370" x2="785" y2="370"/>
      <line x1="30" y1="430" x2="785" y2="430"/>
      <line x1="30" y1="40" x2="30" y2="430"/>
      <line x1="785" y1="40" x2="785" y2="430"/>
    </g>
    <g class="month-labels">
      <text class="axis-label" x="30" y="30">Jan 13</text>
      <text class="axis-label" x="110" y="30">Apr 13</text>
      <text class="axis-label" x="190" y="30">Jul 13</text>
      <text class="axis-label" x="270" y="30">Oct 13</text>
      <text class="axis-label" x="350" y="30">Jan 14</text>
      <text class="axis-label" x="430" y="30">Apr 14</text>
      <text class="axis-label" x="510" y="30">Jul 14</text>
      <text class="axis-label" x="590" y="30">Oct 14</text>
      <text class="axis-label" x="670" y="30">Jan 15</text>
      <text class="axis-label" x="745" y="30">Apr 15</text>
    </g>
    <g class="value-labels">
      <text class="axis-label current" x="790" y="62">23,460</text>
      <text class="axis-label" x="790" y="90">20,000</text>
      <text class="axis-label" x="790" y="148">20,501</text>
      <text class="axis-label" x="790" y="208">18,000</text>
      <text class="axis-label" x="790" y="263">16,000</text>
      <text class="axis-label" x="790" y="300" fill="var(--market-line)">15,204</text>
      <text class="axis-label" x="790" y="318">14,000</text>
      <text class="axis-label" x="790" y="433">10,000</text>
    </g>
    <g class="search-icon" fill="none" stroke="#4a78b8" stroke-width="3">
      <circle cx="825" cy="28" r="9"/>
      <line x1="832" y1="35" x2="842" y2="45"/>
    </g>
    <polyline class="market-line" fill="none" stroke="var(--market-line)" stroke-width="3"
      points="30,430 70,426 110,420 150,412 190,408 230,398 270,392 310,384 350,380 390,372 430,366 470,360 510,352 550,345 590,338 630,330 670,320 710,310 745,300 785,298"/>
    <polyline class="peer-line" fill="none" stroke="var(--peer-line)" stroke-width="2.5"
      points="30,430 70,422 110,412 150,404 190,398 230,384 270,378 310,364 350,360 390,352 430,346 470,340 510,322 550,318 590,300 630,286 670,262 710,234 745,176 785,150"/>
    <polyline class="index-line" fill="none" stroke="var(--index-line)" stroke-width="3"
      points="30,430 70,418 110,408 150,400 190,396 230,376 270,372 310,350 350,346 390,334 430,336 470,318 510,300 550,290 590,266 630,248 670,214 710,184 745,112 785,58"/>
    <circle cx="785" cy="58" r="5" fill="var(--index-line)"/>
    <g class="legend">
      <rect x="22" y="456" width="30" height="6" fill="var(--index-line)"/>
      <text class="legend-label" x="62" y="466">Index performance</text>
      <rect x="335" y="456" width="30" height="6" fill="var(--market-line)"/>
      <text class="legend-label" x="375" y="466">Broadline 500 performance</text>
    </g>
  </svg>

  <div class="pager">
    <span class="pager-dot active"></span>
    <span class="pager-dot"></span>
    <span class="pager-dot"></span>
  </div>

  <nav class="tabs">
    <div class="tab tab-description">Description</div>
    <div class="tab tab-snapshot">Performance<br>snapshot</div>
    <div class="tab tab-components">Components</div>
  </nav>

  <p class="description">This index is based on the data from Corvane Media rankings and includes of brands. Resonant brands is the first &nbsp;global analytical framework to connect human well-beings with brands at business levels</p>
</main>
</body>
</html>
```